Brookvale Estates LLC stationary for a real estate property management company.

Create stationary (letterhead, envelopes, business cards) using Brookvale Estates LLC logo as primary creative element. Stationary design needs to be horizontal, leaving as much space as possible for correspondence copy. See attached Creative Brief and past stationary files for details.

Target Market(s)

Prospective apartment residents and current residents, vendors, and government agencies.

Industry/Entity Type

Property Management

Contact Information for Business Card

Business card employee title: Property Manager. Should include address, phone, fax, email, website, slogan, and Brookvale Estates logo.

Font styles to use
Sans Serif

Colors
0592cd
000000

Requirements
Must have
• Tone should be conservative, institutional, business (i.e. banking, finance, real estate). Must include: address, phone, fax, website, and slogan (see attached Creative Brief). Should be a horizontal design, leaving as much room as possible for letter correspondence copy.
Nice to have
• Please use an Arial or Helvetica style font.
Should not have
• Letterhead layout should leave as much room as possible for copy.

```html
<!DOCTYPE html>
<html lang="en">
<head>
<meta charset="utf-8">
<title>Brookvale Estates LLC Stationery</title>
<link href="https://fonts.googleapis.com/css2?family=Arimo:wght@400;700&family=Open+Sans:wght@400&display=swap" rel="stylesheet">
<style>
  :root {
    --brand-blue: #0a67a6;
    --ink: #333333;
    --ink-soft: #555555;
    --paper: #f7f7f7;
    --paper-white: #ffffff;
    --flap: #434345;
    --backdrop: #e4e2df;
  }
  * { margin: 0; padding: 0; box-sizing: border-box; }
  html, body { width: 1200px; height: 754px; overflow: hidden; }
  body { background: var(--backdrop); font-family: "Arimo", Arial, sans-serif; color: var(--ink); position: relative; }
  .sheet { position: absolute; background: var(--paper); box-shadow: 0 2px 6px rgba(0,0,0,.18); overflow: hidden; }

  .wordmark { display: flex; align-items: center; gap: 6px; color: var(--brand-blue); font-weight: 700; white-space: nowrap; }
  .wordmark .dot { background: var(--brand-blue); flex: none; }
  .wordmark.light { color: var(--paper-white); }
  .wordmark.light .dot { background: var(--paper-white); }

  .icon { width: 7px; height: 7px; fill: var(--brand-blue); flex: none; }
  .contact-line { display: flex; align-items: center; gap: 5px; }

  /* Letterhead */
  .letterhead { left: 36px; top: 32px; width: 489px; height: 689px; background: var(--paper-white); }
  .letterhead .wordmark { position: absolute; left: 58px; top: 62px; font-size: 15px; }
  .letterhead .wordmark .dot { width: 12px; height: 12px; }
  .letterhead .divider { position: absolute; left: 316px; top: 50px; width: 1px; height: 54px; background: #cfcfcf; }
  .letterhead .contact { position: absolute; left: 327px; top: 52px; font-size: 7.6px; line-height: 10px; color: var(--ink); }
  .letterhead .salutation { position: absolute; left: 49px; top: 194px; font-family: "Open Sans", Arial, sans-serif; font-size: 13px; color: var(--ink-soft); }
  .letterhead .body { position: absolute; left: 49px; top: 233px; width: 394px; font-family: "Open Sans", Arial, sans-serif; font-size: 7.4px; line-height: 11.8px; color: var(--ink-soft); text-align: justify; }
  .letterhead .body p { margin-bottom: 11.8px; }
  .letterhead .closing { position: absolute; left: 49px; top: 480px; font-family: "Open Sans", Arial, sans-serif; font-size: 7.4px; color: var(--ink-soft); }
  .letterhead .signature { position: absolute; left: 47px; top: 498px; width: 64px; height: 26px; background: linear-gradient(90deg, #e9e9ec, #d9d9de); border-radius: 3px; }

  .footer-band { position: absolute; left: 0; bottom: 0; width: 100%; height: 18px; background: var(--brand-blue); display: flex; align-items: center; justify-content: center; }
  .footer-band .dot { position: absolute; left: 13px; top: 3px; width: 12px; height: 12px; border-radius: 50%; background: var(--paper-white); }
  .footer-band .url { color: var(--paper-white); font-size: 7.6px; letter-spacing: 1.6px; }

  /* Business card front */
  .card-front { left: 578px; top: 74px; width: 267px; height: 153px; background: #f4f4f4; }
  .card-front .wordmark { position: absolute; left: 15px; top: 19px; font-size: 10px; line-height: 11px; align-items: flex-start; }
  .card-front .wordmark .dot { width: 8px; height: 8px; margin-top: 1.5px; }
  .card-front .wordmark .stack { display: block; }
  .card-front .person { position: absolute; left: 15px; top: 50px; }
  .card-front .name { font-weight: 700; font-size: 9.6px; color: var(--brand-blue); }
  .card-front .title { font-size: 7px; color: var(--ink); margin-top: 1px; }
  .card-front .details { position: absolute; left: 15px; top: 74px; font-size: 6px; line-height: 8px; color: var(--ink); }
  .card-front .details .gap { height: 4px; }
  .card-front .slogan { position: absolute; left: 15px; top: 131px; font-size: 6.4px; font-weight: 700; color: var(--brand-blue); }
  .card-front .disc { position: absolute; left: 133px; top: -12px; width: 186px; height: 186px; border-radius: 50%; background: var(--brand-blue); }

  /* Business card back */
  .card-back { left: 877px; top: 144px; width: 267px; height: 152px; background: #f2f2f2; display: flex; align-items: center; justify-content: center; }
  .card-back .wordmark { font-size: 15px; }
  .card-back .wordmark .dot { width: 12px; height: 12px; }

  /* Envelope back */
  .envelope-back { left: 615px; top: 350px; width: 548px; height: 249px; background: #efefef; }
  .envelope-back svg.flap { position: absolute; left: 0; top: 0; }
  .envelope-back .wordmark { position: absolute; left: 50%; top: 44px; transform: translateX(-50%); font-size: 11.5px; }
  .envelope-back .wordmark .dot { width: 9px; height: 9px; }

  /* Envelope front */
  .envelope-front { left: 547px; top: 471px; width: 550px; height: 250px; background: #f5f5f5; }
  .envelope-front .wordmark { position: absolute; left: 22px; top: 34px; font-size: 14px; }
  .envelope-front .wordmark .dot { width: 11px; height: 11px; }
  .envelope-front .return { position: absolute; left: 38px; top: 68px; font-size: 7.6px; line-height: 9.4px; color: var(--ink); }
</style>
</head>
<body>
<svg width="0" height="0" style="position:absolute">
  <symbol id="i-phone" viewBox="0 0 10 10"><path d="M2 0.5 L3.6 0.5 L4.2 2.8 L3 3.6 Q4 5.8 6.4 7 L7.2 5.8 L9.5 6.4 L9.5 8 Q9.5 9.5 8 9.5 Q0.5 8.8 0.5 2 Q0.5 0.5 2 0.5 Z"/></symbol>
  <symbol id="i-fax" viewBox="0 0 10 10"><rect x="2.5" y="0.5" width="5" height="3"/><rect x="0.5" y="3.8" width="9" height="4" rx="1"/><rect x="2.5" y="6.5" width="5" height="3"/></symbol>
  <symbol id="i-mail" viewBox="0 0 10 10"><rect x="0.5" y="2" width="9" height="6"/><path d="M0.5 2 L5 5.5 L9.5 2" stroke="#fff" stroke-width="0.9" fill="none"/></symbol>
  <symbol id="i-web" viewBox="0 0 10 10"><circle cx="5" cy="5" r="4.5"/><path d="M0.5 5 H9.5 M5 0.5 V9.5" stroke="#fff" stroke-width="0.8"/></symbol>
</svg>

<section class="sheet letterhead">
  <div class="wordmark"><span class="dot"></span>BROOKVALE ESTATES LLC</div>
  <div class="divider"></div>
  <div class="contact">
    <div>2780 Harbor Ridge Drive #B210</div>
    <div>Lakeview, CA 90417</div>
    <div class="contact-line"><svg class="icon"><use href="#i-phone"/></svg>555-314-2760</div>
    <div class="contact-line"><svg class="icon"><use href="#i-fax"/></svg>555-314-2761</div>
    <div class="contact-line"><svg class="icon"><use href="#i-mail"/></svg>daniel@brookvaleestates.us</div>
  </div>
  <div class="salutation">Dear Mr. Ellis,</div>
  <div class="body">
    <p>Lorem ipsum dolor sit amet, consectetur adipiscing elit. Donec orci purus, luctus vitae dignissim eu, iaculis sed purus. Vivamus faucibus, ipsum nec aliquet viverra, leo mauris condimentum ligula, sit amet sagittis enim ligula quis arcu. Nam egestas tortor id nisi porttitor mattis. In tortor ante, ultricies in suscipit a, tempus non massa. Vivamus et auctor mi. Fusce vel massa nulla. Phasellus nec eros mauris, et scelerisque orci.</p>
    <p>Donec malesuada orci vitae nulla accumsan porta a id massa. Quisque accumsan iaculis magna sit amet fringilla. Maecenas consequat, magna eget tincidunt semper, odio nibh rutrum mi, id feugiat ante nisi eu risus. Vestibulum nunc orci, rhoncus a placerat in, ultricies in mi. Cras mattis varius eros, vel fringilla nisi suscipit eget. Quisque scelerisque sagittis nulla at porttitor.</p>
    <p>Sed id augue vitae urna euismod commodo aliquet a quam. Pellentesque arcu velit, cursus et malesuada ut, consequat et diam. Nullam erat sem, rhoncus id ullamcorper vitae, rhoncus et arcu. In ultricies ultricies nulla, ut rutrum nisi iaculis at. Donec eu magna a metus ornare faucibus. Fusce aliquet faucibus ultricies. Morbi semper, est id tincidunt gravida, sem arcu adipiscing lacus, ac bibendum nulla leo eu purus. Quisque nec diam sed risus consectetur a accumsan quis quis nibh. Vestibulum id purus lorem.</p>
    <p>It is a long established fact that a reader will be distracted by the readable content of a page when looking at its layout. The point of using Lorem Ipsum is that it has a more-or-less normal distribution of letters, as opposed to using 'Content here, content here', making it look like readable English. Many desktop publishing packages</p>
  </div>
  <div class="closing">Sincerely,</div>
  <div class="signature" role="img" aria-label="Handwritten signature"></div>
  <div class="footer-band"><span class="dot"></span><span class="url">www.brookvaleestates.us</span></div>
</section>

<section class="sheet card-front">
  <div class="disc"></div>
  <div class="wordmark"><span class="dot"></span><span class="stack">BROOKVALE ESTATES<br>LLC</span></div>
  <div class="person">
    <div class="name">DANIEL WHITFORD</div>
    <div class="title">Property Manager</div>
  </div>
  <div class="details">
    <div>2780 Harbor Ridge Drive #B210</div>
    <div>Lakeview, CA 90417</div>
    <div class="gap"></div>
    <div class="contact-line"><svg class="icon"><use href="#i-phone"/></svg>555-314-2760</div>
    <div class="contact-line"><svg class="icon"><use href="#i-fax"/></svg>555-314-2761</div>
    <div class="contact-line"><svg class="icon"><use href="#i-mail"/></svg>daniel@brookvaleestates.us</div>
    <div class="contact-line"><svg class="icon"><use href="#i-web"/></svg>www.brookvaleestates.us</div>
  </div>
  <div class="slogan">Multifamily Property Management</div>
</section>

<section class="sheet card-back">
  <div class="wordmark"><span class="dot"></span>BROOKVALE ESTATES LLC</div>
</section>

<section class="sheet envelope-back">
  <svg class="flap" width="548" height="96" viewBox="0 0 548 96">
    <path d="M0 0 H548 L538 62 Q532 92 500 92 H48 Q16 92 10 62 Z" fill="var(--flap)"/>
  </svg>
  <div class="wordmark light"><span class="dot"></span>BROOKVALE ESTATES LLC</div>
</section>

<section class="sheet envelope-front">
  <div class="wordmark"><span class="dot"></span>BROOKVALE ESTATES LLC</div>
  <div class="return">
    <div>2780 Harbor Ridge Drive #B210</div>
    <div>Lakeview, CA 90417</div>
  </div>
  <div class="footer-band"><span class="dot"></span><span class="url">www.brookvaleestates.us</span></div>
</section>
</body>
</html>
```